Business Card for Vorla Parts Wholesale supplier

Hi There! I need a new business card for our company. We are specialized in selling Vorla parts, mostly we sell new LCD screens for Zelnar and Drelks. I would like to see that back in the design.

You can find the colors and logo's on our website: www.hartuvo.nl

Industry/Entity Type

Business

Contact Information for Business Card

My Details:
Tobias Lindqvist

Phone: 0031687203316
E-mail: Tobias@hartuvo.nl

Slogan: "Because Quality Matters"

Font styles to use
Sans Serif

Colors

Designer to choose colors to be used in the design.

Requirements
Must have
• A Black backside with the Hartuvo logo on it. The front side should be clean with only my contact details.
• But I'm also open for something really different or awesome!
Nice to have
• Remember that we are in the parts & repairing industry, So i'll be handing those business cards mainly to repair companies. Maybe you can do something with that thought :)

```html
<!DOCTYPE html>
<html lang="en">
<head>
<meta charset="utf-8">
<title>Hartuvo Business Card</title>
<link rel="stylesheet" href="https://fonts.googleapis.com/css2?family=Roboto:wght@400;500;700&family=PT+Sans:wght@400&display=swap">
<style>
  :root {
    --page-bg: #e6e6e6;
    --card-dark: #1f1f1f;
    --card-dark-deep: #161616;
    --card-light: #fafafa;
    --orange: #e8661c;
    --ink: #1b1b1b;
    --ink-soft: #333333;
    --rule: #8a8a8a;
    --white: #ffffff;
  }
  * { box-sizing: border-box; margin: 0; padding: 0; }
  html, body {
    width: 1200px; height: 576px; overflow: hidden;
    background: var(--page-bg);
    font-family: "Roboto", Arial, sans-serif;
  }
  .canvas { position: relative; width: 1200px; height: 576px; }

  .card {
    position: absolute;
    top: 138px;
    border-radius: 12px;
    overflow: hidden;
    box-shadow: 0 3px 8px rgba(0,0,0,0.25);
  }

  /* Back side */
  .card-back {
    left: 82px; width: 484px; height: 294px;
    background: var(--card-dark);
  }
  .back-photo {
    position: absolute; inset: 0;
    background:
      radial-gradient(ellipse 60% 55% at 62% 28%, #3a3a3a 0%, #2a2a2a 45%, rgba(31,31,31,0) 80%),
      linear-gradient(160deg, #262626 0%, #1c1c1c 60%, var(--card-dark-deep) 100%);
  }
  .back-brand {
    position: absolute; left: 104px; top: 116px;
    display: flex; align-items: center; gap: 14px;
  }
  .brand-square {
    width: 56px; height: 60px;
    background: var(--orange);
    border-radius: 4px;
  }
  .brand-name {
    font-family: "Roboto", Arial, sans-serif;
    font-weight: 700;
    font-size: 56px;
    line-height: 1;
    letter-spacing: 1px;
  }
  .back-brand .brand-name { color: var(--white); }

  /* Front side */
  .card-front {
    left: 602px; width: 482px; height: 292px;
    background: linear-gradient(180deg, var(--white) 0%, var(--card-light) 55%, #eeeeee 100%);
  }
  .front-brand {
    position: absolute; left: 20px; top: 34px;
    display: flex; align-items: center; gap: 14px;
  }
  .front-brand .brand-square { width: 62px; height: 68px; }
  .front-brand .brand-name { color: var(--ink); font-size: 64px; }

  .holder {
    position: absolute; right: 22px; top: 148px;
    text-align: right;
  }
  .holder-name {
    color: var(--orange);
    font-weight: 700;
    font-size: 17px;
  }
  .holder-role {
    color: var(--ink-soft);
    font-size: 11px;
    margin-top: 5px;
  }
  .divider {
    position: absolute; left: 19px; top: 178px;
    width: 336px; height: 1px; background: var(--rule);
  }

  .contacts {
    position: absolute; left: 22px; top: 206px;
    list-style: none;
  }
  .contacts li {
    display: flex; align-items: center; gap: 9px;
    font-size: 12px; color: var(--ink);
    height: 17px;
  }
  .contacts svg { width: 11px; height: 11px; fill: var(--orange); flex: none; }

  .footer-band {
    position: absolute; left: 0; bottom: 0;
    width: 100%; height: 17px; background: var(--ink);
  }
  .slogan-band {
    position: absolute; right: 0; bottom: 0;
    width: 200px; height: 36px;
    background: var(--orange);
    clip-path: polygon(16px 0, 100% 0, 100% 100%, 0 100%);
    display: flex; align-items: center; justify-content: center;
    padding-left: 14px;
  }
  .slogan {
    font-family: "PT Sans", Arial, sans-serif;
    color: var(--white);
    font-size: 11.5px;
  }
</style>
</head>
<body>
<main class="canvas">

  <section class="card card-back" aria-label="Card back">
    <div class="back-photo" role="img" aria-label="Dark close-up photo of a phone with a cracked screen"></div>
    <div class="back-brand">
      <span class="brand-square"></span>
      <span class="brand-name">hartuvo</span>
    </div>
  </section>

  <section class="card card-front" aria-label="Card front">
    <div class="front-brand">
      <span class="brand-square"></span>
      <span class="brand-name">hartuvo</span>
    </div>

    <div class="holder">
      <p class="holder-name">Tobias Lindqvist</p>
      <p class="holder-role">Managing Director</p>
    </div>
    <div class="divider"></div>

    <ul class="contacts">
      <li>
        <svg viewBox="0 0 16 16" aria-hidden="true"><path d="M2 5c0-2 2-3 6-3s6 1 6 3v1h-3V5H5v1H2zM4 7h8l2 7H2zM8 9a2 2 0 1 0 0 4 2 2 0 0 0 0-4z"/></svg>
        0031687203316
      </li>
      <li>
        <svg viewBox="0 0 16 16" aria-hidden="true"><path d="M8 1a7 7 0 1 0 0 14A7 7 0 0 0 8 1zm0 1.5c.8 0 1.7 1.6 2 4H6c.3-2.4 1.2-4 2-4zM2.6 7.5h2c0 .9.1 1.7.3 2.5h-2a5.5 5.5 0 0 1-.3-2.5zm8.8 0h2a5.5 5.5 0 0 1-.3 2.5h-2c.2-.8.3-1.6.3-2.5zM6 8.5h4c-.3 2.6-1.2 5-2 5s-1.7-2.4-2-5z"/></svg>
        Tobias@hartuvo.nl
      </li>
      <li>
        <svg viewBox="0 0 16 16" aria-hidden="true"><path d="M1 3h14v10H1zm1.5 1.2L8 8.5l5.5-4.3V4h-11z"/></svg>
        www.hartuvo.nl
      </li>
    </ul>

    <div class="footer-band"></div>
    <div class="slogan-band"><span class="slogan">Because Quality Matters</span></div>
  </section>

</main>
</body>
</html>
```